Building company buisness cards

We are looking for a sharp modern new look for our business cards.
We are a New Zealand based company that specialises in house and land packages.
We have attached a photo of the current logo and would like to see if it can be improved somehow if needed.
We are open to any colours but we have chosen green at this stage.
Feel free to change the font and make the logo smarter looking.
Play with the colours and see what looks best.

We want a card that looks so good know one will want to throw it away!

Target Market(s)

Home buyers

Industry/Entity Type

Building

Contact Information for Business Card

Derek Tolvane
0217394062
dtolvane@quillmarkhomesteads.co.nz
quillmarkhomesteads.co.nz

Font styles to use
Serif
Sans Serif

Colors

Designer to choose colors to be used in the design.

Requirements
Must have
• Logo and company name on one side, details on the other side
Nice to have
• Color codes for the original green are HEX #4a8028, RGB(74,128,40), CMYK(42,0,69,50)
• Round corners, Raised and/or spot UV

```html
<!DOCTYPE html>
<html lang="en">
<head>
<meta charset="utf-8">
<title>Quillmark Homesteads – Business Cards</title>
<link rel="stylesheet" href="https://fonts.googleapis.com/css2?family=Open+Sans:wght@400;600;700;800&display=swap">
<style>
  :root {
    --backdrop: #2b2c2e;
    --green-light: #8ce84a;
    --green-mid: #6cc23a;
    --green-deep: #4a8a28;
    --brand-green: #4a8028;
    --paper: #ffffff;
    --ink-grey: #6a6a6a;
    --rule: #d6d6d6;
  }
  * { box-sizing: border-box; margin: 0; padding: 0; }
  html, body { width: 1200px; height: 885px; overflow: hidden; }
  body {
    background: var(--backdrop);
    font-family: "Open Sans", Arial, sans-serif;
    position: relative;
  }
  .card {
    position: absolute;
    width: 560px;
    height: 320px;
    border-radius: 6px;
    overflow: hidden;
    box-shadow: 0 14px 30px rgba(0,0,0,0.45);
  }
  /* Front of card */
  .card-front {
    left: 80px;
    top: 90px;
    background: linear-gradient(135deg, var(--green-light) 0%, var(--green-mid) 45%, var(--green-deep) 100%);
    color: var(--paper);
  }
  .front-brand {
    position: absolute;
    left: 0; right: 0; top: 118px;
    display: flex;
    align-items: center;
    justify-content: center;
    gap: 12px;
  }
  .brand-dot {
    width: 18px; height: 18px;
    border-radius: 50%;
    background: var(--paper);
  }
  .front-brand-name {
    font-weight: 800;
    font-size: 30px;
    letter-spacing: 0.5px;
  }
  .front-url {
    position: absolute;
    left: 0; right: 0; bottom: 48px;
    text-align: center;
    font-size: 14px;
    letter-spacing: 3.5px;
  }
  /* Back of card */
  .card-back {
    left: 560px;
    top: 480px;
    background: var(--paper);
  }
  .back-band {
    position: absolute;
    left: 0; top: 0; right: 0;
    height: 110px;
    background: var(--brand-green);
  }
  .holder-name {
    position: absolute;
    right: 32px; top: 24px;
    color: var(--paper);
    font-weight: 700;
    font-size: 19px;
    letter-spacing: 0.3px;
  }
  .back-brand {
    position: absolute;
    left: 36px; top: 128px;
    color: var(--brand-green);
    font-weight: 800;
    font-size: 32px;
    line-height: 1;
  }
  .back-brand-rule {
    position: absolute;
    left: 36px; top: 176px;
    width: 120px; height: 1px;
    background: var(--rule);
  }
  .contact {
    position: absolute;
    left: 36px; bottom: 34px;
    font-size: 14px;
    line-height: 1.45;
    color: var(--ink-grey);
  }
  .contact-label {
    color: var(--brand-green);
    font-weight: 700;
  }
</style>
</head>
<body>
  <section class="card card-front" aria-label="Card front">
    <div class="front-brand">
      <span class="brand-dot"></span>
      <span class="front-brand-name">quillmark homesteads</span>
    </div>
    <p class="front-url">www.quillmarkhomesteads.co.nz</p>
  </section>

  <section class="card card-back" aria-label="Card back">
    <div class="back-band"></div>
    <p class="holder-name">DEREK TOLVANE</p>
    <p class="back-brand">quillmark homesteads.</p>
    <div class="back-brand-rule"></div>
    <div class="contact">
      <p><span class="contact-label">Phone:</span> 0217394062</p>
      <p>dtolvane@quillmarkhomesteads.co.nz</p>
    </div>
  </section>
</body>
</html>
```